IRON PEAK TRAINING- Shooting Range!!!And virtual shooting range!!!

We are looking to do a clean cut web page for shooting range. We have indoor shooting simulator, retail store that sales accessories and pistols, rifles and shot guns. We are membership based for indoor shooting range Only and virtual shooting is open to public as well as retail store. We also specialize in shooting training classes and CWP classes.
Updates

Thank you for your patience. We are working with a busy travel schedule. We will be making final decisions tomorrow and moving forward with getting this launched. Regards, Gerald

Target Market(s)

Public and private entertainment

Industry/Entity Type

Training

Number of Pages Required

5+ page

Font styles to use
Sans Serif

Requirements
Must have
• Clean and easy approach we really like the website our friend has www.valormarkline.com please take a look at a lay out. We would like to also add onli member schedule that is available for shooting sections and that they can access and book them selvs.
Nice to have
• White, black, gray or red colors

```html
<!DOCTYPE html>
<html lang="en">
<head>
<meta charset="utf-8">
<title>Iron Peak Training – Shooting Range</title>
<link href="https://fonts.googleapis.com/css2?family=Open+Sans:wght@400;600;700&display=swap" rel="stylesheet">
<style>
:root{
  --bg:#0b0b0b;
  --red:#c20f1f;
  --red-dark:#9e0a17;
  --card:#262626;
  --footer:#1e1e1e;
  --footer-dark:#141414;
  --text:#e8e8e8;
  --muted:#9a9a9a;
  --btn-gray:#3c3c3c;
}
*{box-sizing:border-box;margin:0;padding:0}
html,body{width:732px;height:1200px;overflow:hidden}
body{background:var(--bg);font-family:'Open Sans',sans-serif;color:var(--text);position:relative}
.abs{position:absolute}
.top-rule{left:0;top:0;width:732px;height:2px;background:var(--red)}
.brand{left:37px;top:22px;display:flex;align-items:center;gap:7px}
.brand-mark{width:22px;height:22px;background:var(--red)}
.brand-name{font-weight:700;font-size:12px;line-height:1.1;color:#d9d9d9;width:80px}
.btn{display:flex;align-items:center;justify-content:center;font-size:9px;color:#fff;text-decoration:none}
.btn-red{background:var(--red);box-shadow:0 1px 0 #600}
.btn-gray{background:var(--btn-gray)}
.nav{left:37px;top:64px;width:658px;height:31px;border-bottom:2px solid #3a3a3a}
.nav a{position:absolute;top:0;height:29px;line-height:29px;font-size:7.6px;color:#cfcfcf;text-decoration:none;text-align:center}
.nav a.active{background:#2c2c2c;border-top:2px solid var(--red);color:#fff;line-height:27px}
.slider{left:37px;top:103px;width:462px;height:282px;background:
  linear-gradient(90deg,#6d6d6a 0%,#9c9c97 12%,#d4d4cc 35%,#e0e0d8 50%,#cfcfc7 65%,#8f8f8a 88%,#5e5e5a 100%)}
.slider-arrow{width:17px;height:17px;border-radius:50%;background:rgba(120,120,120,.6);top:132px}
.slider-arrow svg{display:block}
.caption{left:25px;top:225px;width:306px;height:33px;background:rgba(20,20,20,.85);font-size:11px;line-height:33px;padding-left:11px;color:#fff}
.booking{left:511px;top:103px;width:186px;height:282px;background:var(--red)}
.booking h2{position:absolute;left:0;width:186px;top:11px;text-align:center;font-weight:400;font-size:14px;color:#fff}
.booking label{position:absolute;font-size:9.5px;line-height:12px;color:#fff}
.booking .field{position:absolute;height:21px;border:1px solid #f1c0c4}
.booking .field svg{position:absolute;right:6px;top:5px}
.booking .book{position:absolute;left:89px;top:238px;width:88px;height:25px;font-size:10px;background:var(--red-dark);box-shadow:0 1px 2px rgba(0,0,0,.4)}
.welcome-title{left:0;width:732px;top:409px;text-align:center;font-size:13.5px;font-weight:400}
.welcome-text{left:42px;width:648px;top:436px;text-align:center;font-size:7.5px;line-height:12.4px;color:var(--muted)}
.read-more{left:322px;top:499px;width:86px;height:18px;font-size:7.5px}
.feature{top:552px;width:220px;text-align:center}
.feature .photo{width:150px;height:78px;margin:0 auto}
.feature h3{font-size:11.5px;font-weight:600;margin-top:9px}
.feature p{font-size:7.5px;line-height:11px;color:var(--muted);margin:6px auto 0;width:205px}
.products-title{left:36px;top:707px;font-size:14px;font-weight:400}
.card{top:738px;width:151px;height:177px;background:var(--card)}
.card .photo{position:absolute;left:4px;top:4px;width:143px;height:102px;background:radial-gradient(ellipse at 50% 50%,#cfcfcf 0%,#ececec 45%,#fff 75%)}
.card h4{position:absolute;top:113px;width:151px;text-align:center;font-size:10px;font-weight:600}
.card .price{position:absolute;top:130px;width:151px;text-align:center;font-size:9px}
.card .price s{color:#7a7a7a;margin-right:6px}
.card .btn{position:absolute;left:46px;top:148px;width:58px;height:18px}
.cta{left:0;top:966px;width:732px;height:37px;background:var(--red)}
.cta p{position:absolute;left:93px;top:11px;font-size:10.5px;white-space:nowrap;color:#f4d7da}
.cta .btn{position:absolute;left:530px;top:8px;width:80px;height:22px;background:#3a3a3a;font-size:9.5px}
.footer{left:0;top:1003px;width:732px;height:160px;background:var(--footer)}
.footer h5{position:absolute;top:25px;font-size:8px;font-weight:600;color:#fff}
.footer p,.footer li{font-size:6.8px;line-height:9.6px;color:#a8a8a8}
.footer ul{list-style:none}
.footer .links li{position:relative;padding-left:13px;line-height:13px}
.footer .links li::before{content:"";position:absolute;left:1px;top:5px;width:3px;height:3px;border-radius:50%;background:#999}
.footer .links li.on{color:#fff}
.footer .info li{display:flex;align-items:center;gap:6px;line-height:12.7px}
.footer .select{position:absolute;left:563px;width:131px;height:18px;background:#333;border:1px solid #3c3c3c;font:6.8px 'Open Sans',sans-serif;color:#aaa;padding-left:6px;display:flex;align-items:center}
.footer .select svg{position:absolute;right:6px;top:6px}
.footer .send{position:absolute;left:643px;top:126px;width:50px;height:14px;font-size:7px;font-weight:600}
.bottom{left:0;top:1163px;width:732px;height:37px;background:var(--footer-dark)}
.bottom p{position:absolute;left:37px;top:15px;font-size:6.8px;color:#8a8a8a}
.social{position:absolute;top:14px;display:flex;gap:11px;left:631px}
.social span{width:8px;height:8px;border-radius:50%;background:#d6d6d6}
</style>
</head>
<body>
<div class="abs top-rule"></div>

<div class="abs brand"><span class="brand-mark"></span><span class="brand-name">IRON PEAK TRAINING</span></div>

<a class="abs btn btn-red" style="left:507px;top:22px;width:92px;height:20px">Login &nbsp;/&nbsp; Register</a>
<a class="abs btn btn-gray" style="left:603px;top:22px;width:92px;height:20px">Contact</a>

<nav class="abs nav">
  <a class="active" style="left:348px;width:40px">HOME</a>
  <a style="left:398px;width:40px">ABOUT</a>
  <a style="left:448px;width:44px">CLASSES</a>
  <a style="left:504px;width:52px">LOCATIONS</a>
  <a style="left:570px;width:36px">STORE</a>
  <a style="left:618px;width:40px">RANGE</a>
</nav>

<section class="abs slider" role="img" aria-label="Photo of an indoor shooting lane with paper targets at the far end">
  <div class="abs slider-arrow" style="left:10px"><svg width="17" height="17"><path d="M10 4 L6 8.5 L10 13" stroke="#ddd" stroke-width="1.5" fill="none"/></svg></div>
  <div class="abs slider-arrow" style="left:435px"><svg width="17" height="17"><path d="M7 4 L11 8.5 L7 13" stroke="#ddd" stroke-width="1.5" fill="none"/></svg></div>
  <div class="abs caption">Aliquam sed lobortis velit. Etiam quis gravida augue</div>
</section>

<form class="abs booking">
  <h2>Online Member Booking</h2>
  <label style="left:9px;top:46px">Name:</label>
  <div class="field" style="left:9px;top:62px;width:168px"></div>
  <label style="left:9px;top:92px">Email:</label>
  <div class="field" style="left:9px;top:108px;width:168px"></div>
  <label style="left:9px;top:138px">Phone Number:</label>
  <div class="field" style="left:9px;top:154px;width:168px"></div>
  <label style="left:9px;top:182px">Date:</label>
  <div class="field" style="left:9px;top:198px;width:68px;height:22px">
    <svg width="10" height="10" viewBox="0 0 10 10"><rect x="0.5" y="1.5" width="9" height="8" fill="none" stroke="#fff"/><path d="M0.5 4h9M3 0v3M7 0v3" stroke="#fff"/></svg>
  </div>
  <label style="left:101px;top:182px">Time:</label>
  <div class="field" style="left:101px;top:198px;width:76px;height:22px">
    <svg width="10" height="10" viewBox="0 0 10 10"><circle cx="5" cy="5" r="4.2" fill="none" stroke="#fff" stroke-width="1.2"/><path d="M5 2.5V5h2" stroke="#fff" fill="none"/></svg>
  </div>
  <a class="btn book">Book Now</a>
</form>

<h1 class="abs welcome-title">Welcome To Our Site</h1>
<p class="abs welcome-text">Lorem ipsum dolor sit amet, consectetur adipiscing elit. Aliquam sapien justo, finibus nec porttitor eu, iaculis vel massa. Vestibulum lectus lacus, porta at lobortis quis, ornare vel lectus. Donec ut neque sed nisi sagittis ultricies. Donec facilisis neque turpis, eu convallis felis pharetra non. In magna mauris, congue id dignissim at, accumsan quis augue. Vestibulum lacinia interdum ipsum. Pellentesque malesuada facilisis sapien, ut tristique tortor consectetur vel. Vivamus malesuada neque in quam aliquam mattis. Aenean sed ipsum congue, aliquet tortor ac, tempor ligula. Vestibulum facilisis ex et ex convallis iaculis.</p>
<a class="abs btn btn-red read-more">Read More</a>

<div class="abs feature" style="left:29px">
  <div class="photo" role="img" aria-label="Photo of an indoor shooting lane" style="background:linear-gradient(90deg,#6a6a6a,#a9a9a4 20%,#d2d2cc 50%,#a9a9a4 80%,#6a6a6a)"></div>
  <h3>Indoor shooting simulator</h3>
  <p>Mauris efficitur consequat laoreet. Phasellus sed purus ipsum. Pellentesque sed enim libero.</p>
</div>
<div class="abs feature" style="left:256px">
  <div class="photo" role="img" aria-label="Photo of rifles and pistols on a store wall" style="background:linear-gradient(180deg,#9a9a9a,#5a5a5a 40%,#3a3a3a 65%,#a0a0a0)"></div>
  <h3>Retail store</h3>
  <p>Mauris efficitur consequat laoreet. Phasellus sed purus ipsum. Pellentesque sed enim libero.</p>
</div>
<div class="abs feature" style="left:483px">
  <div class="photo" role="img" aria-label="Photo of two trainees in tactical gear during a shooting class" style="background:linear-gradient(180deg,#4a4d52,#25272a 55%,#4a4c50)"></div>
  <h3>Shooting training classes and CWP</h3>
  <p>Mauris efficitur consequat laoreet. Phasellus sed purus ipsum. Pellentesque sed enim libero.</p>
</div>

<h2 class="abs products-title">Our Products</h2>

<div class="abs card" style="left:37px">
  <div class="photo" role="img" aria-label="Product photo of a semi-automatic pistol"></div>
  <h4>Lorem ipsum dolor</h4>
  <div class="price"><s>$598.00</s>$580.00</div>
  <a class="btn btn-red">More</a>
</div>
<div class="abs card" style="left:206px">
  <div class="photo" role="img" aria-label="Product photo of a compact submachine gun"></div>
  <h4>Lorem ipsum dolor</h4>
  <div class="price"><s>$598.00</s>$580.00</div>
  <a class="btn btn-gray">More</a>
</div>
<div class="abs card" style="left:375px">
  <div class="photo" role="img" aria-label="Product photo of an antique flintlock pistol" style="background:radial-gradient(ellipse at 50% 50%,#d8cbb4 0%,#eee8de 45%,#fff 75%)"></div>
  <h4>Lorem ipsum dolor</h4>
  <div class="price"><s>$598.00</s>$580.00</div>
  <a class="btn btn-gray">More</a>
</div>
<div class="abs card" style="left:545px">
  <div class="photo" role="img" aria-label="Product photo of a pistol with ammunition"></div>
  <h4>Lorem ipsum dolor</h4>
  <div class="price"><s>$598.00</s>$580.00</div>
  <a class="btn btn-gray">More</a>
</div>

<section class="abs cta">
  <p>Lorem ipsum dolor sit amet, consectetur adipiscing elit. Aliquam sapien justo, finibus nec</p>
  <a class="btn">Join Now</a>
</section>

<footer class="abs footer">
  <h5 style="left:37px">WHO WE ARE</h5>
  <p class="abs" style="left:37px;top:46px;width:142px">Lorem ipsum dolor sit amet, consectetur adipiscing elit. Nullam venenatis velit blandit est condimentum aliquet. Curabitur ut libero justo. Nulla ut ex facilisis, tincidunt quam vitae, iaculis orci. Nullam eu faucibus nibh.</p>
  <p class="abs" style="left:143px;top:113px;display:flex;align-items:center;gap:4px;color:#888">More
    <svg width="9" height="9" viewBox="0 0 9 9"><circle cx="4.5" cy="4.5" r="4" fill="none" stroke="#888" stroke-width=".8"/><path d="M2.5 4.5h4M5 3l1.5 1.5L5 6" stroke="#888" stroke-width=".8" fill="none"/></svg></p>

  <h5 style="left:241px">USEFUL LINKS</h5>
  <ul class="abs links" style="left:241px;top:45px">
    <li class="on">HOME</li><li>ABOUT</li><li>CLASSES</li><li>LOCATIONS</li><li>STORE</li><li>RANGE</li>
  </ul>

  <h5 style="left:373px">GET IN TOUCH</h5>
  <p class="abs" style="left:373px;top:46px;width:145px">Doloreiur quia commolu ptatemp dolupta orepreum tibusam eumenis et consent acculignis dentibea</p>
  <ul class="abs info" style="left:374px;top:81px">
    <li><svg width="6" height="8" viewBox="0 0 6 8"><path d="M3 8C1 5 0 4 0 3a3 3 0 016 0c0 1-1 2-3 5z" fill="#bbb"/><circle cx="3" cy="3" r="1" fill="#1e1e1e"/></svg>84 Street, City, State 24813</li>
    <li><svg width="7" height="7" viewBox="0 0 7 7"><path d="M1 0l1.5 1.8-.8 1a4 4 0 002.5 2.5l1-.8L7 6 5.8 7C3 7 0 4 0 1.2z" fill="#bbb"/></svg>(555) 20 - 418 - 7730</li>
    <li><svg width="7" height="6" viewBox="0 0 7 6"><rect width="7" height="6" fill="#bbb"/><path d="M0 0l3.5 3L7 0" stroke="#1e1e1e" fill="none" stroke-width=".8"/></svg>hello@ironpeakrange.com</li>
  </ul>

  <h5 style="left:563px">CONTACT</h5>
  <p class="abs" style="left:563px;top:46px;width:130px">Doloreiur quia commolu ptatemp dolupta orepreum</p>
  <div class="select" style="top:74px">Email</div>
  <div class="select" style="top:98px">Contact For
    <svg width="7" height="5" viewBox="0 0 7 5"><path d="M.5 .5L3.5 3.5 6.5 .5" stroke="#bbb" fill="none"/></svg></div>
  <a class="btn btn-red send">CONTACT</a>
</footer>

<div class="abs bottom">
  <p>© 2015 ironpeakrange. All rights reserved.</p>
  <div class="social"><span></span><span></span><span></span><span></span></div>
</div>
</body>
</html>
```